Dancing Emoji Lady but make it silhouette

We need a main image for the front of a hard wine seltzer. The best emoji that would describe this brand is the dancing lady in red dress emoji. We want to re-create the essence of this emoji in a silhouette (like an outline) so it's our own design, but it captures the fun and flirtatiousness of that emoji. We have three flavors - peach (peach color), fruit punch (red/purple color), and citrus (orange color) - so the only color should be the outline of her swooshing dress.

I'm attaching an image of the emoji I wish to emulate, and then some examples of what I mean by "silhouette" - I know the attached examples are not of a woman dancing, but it's the line/style that I want to emulate here to make a silhouette of the dancer emoji.

```html
<!DOCTYPE html>
<html lang="en">
<head>
<meta charset="utf-8">
<title>Lumo Peach Bellini – Can Label</title>
<link rel="stylesheet" href="https://fonts.googleapis.com/css2?family=Fraunces:opsz,wght@9..144,600&family=Oswald:wght@400;500&display=swap">
<style>
  :root {
    --page: #ebebeb;
    --peach: #f9a691;
    --brown: #6b1a08;
    --white: #ffffff;
    --dress-red: #b02232;
    --dress-soft: #e5685f;
  }
  * { box-sizing: border-box; margin: 0; padding: 0; }
  html, body { width: 1200px; height: 738px; overflow: hidden; }
  body {
    background: var(--page);
    display: flex;
    align-items: center;
    justify-content: center;
  }
  .label {
    position: relative;
    width: 372px;
    height: 600px;
    background: var(--peach);
    color: var(--brown);
    text-align: center;
  }
  .brand-name {
    position: absolute;
    left: 0; right: 0;
    top: 82px;
    font-family: "Oswald", "Arial Narrow", sans-serif;
    font-weight: 500;
    font-size: 40px;
    line-height: 1;
    letter-spacing: 8px;
    padding-left: 8px;
    color: var(--brown);
  }
  .dancer-illustration {
    position: absolute;
    left: 94px;
    top: 167px;
    width: 172px;
    height: 229px;
    border-radius: 40% 40% 30% 30%;
    background: radial-gradient(ellipse at 55% 55%, var(--dress-red) 0%, var(--dress-soft) 45%, var(--peach) 75%);
  }
  .flavor-name {
    position: absolute;
    left: 0; right: 0;
    top: 408px;
    font-family: "Oswald", "Arial Narrow", sans-serif;
    font-weight: 400;
    font-size: 34px;
    line-height: 1;
    letter-spacing: 0.5px;
    color: var(--white);
    transform: scaleY(1.1);
  }
  .product-type {
    position: absolute;
    left: 0; right: 0;
    top: 450px;
    font-family: "Fraunces", Georgia, serif;
    font-weight: 600;
    font-size: 16px;
    line-height: 1;
    color: var(--brown);
  }
  .claims {
    position: absolute;
    left: 0; right: 0;
    top: 476px;
    height: 40px;
  }
  .claim-badge {
    position: absolute;
    top: 2px;
    width: 36px;
    height: 36px;
    border: 1.2px solid var(--brown);
    border-radius: 50%;
    display: flex;
    flex-direction: column;
    align-items: center;
    justify-content: center;
    font-family: "Oswald", "Arial Narrow", sans-serif;
    font-weight: 500;
    font-size: 5.5px;
    line-height: 1.15;
    letter-spacing: 0.2px;
  }
  .claim-badge--calories { left: 104px; }
  .claim-badge--sugar { left: 233px; }
  .claim-main {
    position: absolute;
    left: 0; right: 0;
    top: 5px;
    font-family: "Oswald", "Arial Narrow", sans-serif;
    font-weight: 500;
    font-size: 10px;
    line-height: 1.5;
    letter-spacing: 0.2px;
  }
  .volume {
    position: absolute;
    left: 0; right: 0;
    top: 522px;
    font-family: "Oswald", "Arial Narrow", sans-serif;
    font-weight: 500;
    font-size: 10px;
    letter-spacing: 0.2px;
  }
</style>
</head>
<body>
  <main class="label">
    <h1 class="brand-name">LUMO</h1>

    <div class="dancer-illustration" role="img" aria-label="Single-line drawing of a woman dancing in a swirling red dress, raising a glass of wine"></div>

    <h2 class="flavor-name">PEACH BELLINI</h2>
    <p class="product-type">Hard Wine Seltzer</p>

    <div class="claims">
      <div class="claim-badge claim-badge--calories"><span>ONLY 120</span><span>CALORIES</span></div>
      <p class="claim-main">MADE WITH<br>ORGANIC GRAPES</p>
      <div class="claim-badge claim-badge--sugar"><span>NO ADDED</span><span>SUGAR</span></div>
    </div>

    <p class="volume">6% ABV &nbsp;|&nbsp; 250 mL</p>
  </main>
</body>
</html>
```